Business card for Luxury Portable Restroom Trailer company

We are a Luxury Portable Restroom Trailer Company Called FALCRIDGE HIRES. Based in Orange County California. We provide portable restroom trailers for events, such as, Weddings, Concerts, Charity events, Sporting events, Tournaments, Corporate events, ect. We rent and Sell the Luxury restrooms. Our colors are white, grey, and Orange. As you will see in the logo we uploaded.
There are 2 people in the company so the names and titles will change for the 3 people but card will remain the same. Here is the information for each Person: Dwight Penner CFO 555 318-0476
next Person: Leon Marchetti VP 555 318-0476
Next Person: Owen Marchetti CEO 555 318-0476
Information to include on the card: Luxury Restroom Trailers Rental and Sales. Weddings, Concerts, Charity, Sporting and Corp. Events.

```html
<!DOCTYPE html>
<html lang="en">
<head>
<meta charset="utf-8">
<title>Falcridge Hires – Business Cards</title>
<link rel="stylesheet" href="https://fonts.googleapis.com/css2?family=Montserrat:wght@600;700&family=Encode+Sans+Condensed:wght@500&family=Encode+Sans+Semi+Condensed:wght@500&display=swap">
<style>
  :root {
    --board: #1a1b1d;
    --orange: #f27022;
    --grey: #5b5a56;
    --faint: #d9d9d9;
    --white: #ffffff;
    --edge: #1f1f1f;
  }
  html, body {
    margin: 0;
    padding: 0;
    width: 1193px;
    height: 1200px;
    overflow: hidden;
    background: var(--board);
  }
  .board {
    position: relative;
    width: 1193px;
    height: 1200px;
  }
  .card {
    position: absolute;
    overflow: hidden;
  }
  /* Front */
  .card--front {
    left: 50px; top: 161px;
    width: 500px; height: 278px;
    background: var(--orange);
  }
  .front-mark {
    position: absolute;
    left: 170px; top: 36px;
    width: 158px; height: 150px;
    box-sizing: border-box;
    border: 7px solid var(--grey);
    border-radius: 50%;
  }
  .front-name {
    position: absolute;
    left: 0; right: 0; top: 205px;
    text-align: center;
    font: 700 26px/1 "Montserrat", sans-serif;
    letter-spacing: 1px;
    color: var(--white);
  }
  /* Back */
  .card--back {
    width: 487px; height: 273px;
    background: var(--white);
  }
  .card--cfo { left: 649px; top: 161px; }
  .card--ceo { left: 57px; top: 763px; }
  .card--vp  { left: 656px; top: 763px; }
  .back-band {
    position: absolute;
    left: 0; top: 0;
    width: 487px; height: 273px;
  }
  .back-logo {
    position: absolute;
    left: 0; width: 487px; top: 22px;
    text-align: center;
    font: 700 22px/1 "Montserrat", sans-serif;
    color: var(--grey);
    letter-spacing: 0.5px;
  }
  .ghost-mark {
    position: absolute;
    left: 373px; top: 45px;
    width: 74px; height: 72px;
    box-sizing: border-box;
    border: 3px solid var(--faint);
    border-radius: 50%;
  }
  .ghost-name {
    position: absolute;
    left: 340px; width: 140px; top: 124px;
    text-align: center;
    font: 700 11px/1 "Montserrat", sans-serif;
    color: var(--faint);
  }
  .contact {
    position: absolute;
    right: 26px;
    text-align: right;
    color: var(--grey);
  }
  .contact-line {
    font-family: "Encode Sans Condensed", sans-serif;
    font-weight: 500;
    line-height: 1;
    letter-spacing: -0.5px;
    white-space: nowrap;
  }
  .services {
    position: absolute;
    right: 26px;
    text-align: right;
    color: var(--grey);
    white-space: nowrap;
  }
  .card--cfo .contact { top: 176px; }
  .card--cfo .contact-line { font-size: 21px; }
  .card--cfo .services {
    top: 219px;
    font: 500 14px/21px "Encode Sans Semi Condensed", sans-serif;
    letter-spacing: -0.4px;
  }
  .card--ceo .contact, .card--vp .contact { top: 196px; }
  .card--ceo .contact-line, .card--vp .contact-line { font-size: 23px; }
  .card--ceo .services, .card--vp .services {
    top: 230px;
    font: 600 12px/16px "Montserrat", sans-serif;
  }
</style>
</head>
<body>
<main class="board">

  <section class="card card--front" aria-label="Card front">
    <div class="front-mark"></div>
    <div class="front-name">FALCRIDGE HIRES</div>
  </section>

  <section class="card card--back card--cfo" aria-label="Card back, CFO">
    <svg class="back-band" viewBox="0 0 487 273" aria-hidden="true">
      <polygon points="0,76 348,76 0,268" fill="var(--orange)"/>
      <line x1="348" y1="76" x2="0" y2="268" stroke="var(--edge)" stroke-width="1"/>
    </svg>
    <div class="back-logo">FALCRIDGE HIRES</div>
    <div class="ghost-mark"></div>
    <div class="ghost-name">FALCRIDGE HIRES</div>
    <div class="contact"><div class="contact-line">Dwight Penner CFO 555 318-0476</div></div>
    <div class="services">Luxury Restroom Trailers Rental and Sales.<br>Weddings, Concerts, Charity, Sporting and Corp. Events.</div>
  </section>

  <section class="card card--back card--ceo" aria-label="Card back, CEO">
    <svg class="back-band" viewBox="0 0 487 273" aria-hidden="true">
      <polygon points="0,76 348,76 0,268" fill="var(--orange)"/>
      <line x1="348" y1="76" x2="0" y2="268" stroke="var(--edge)" stroke-width="1"/>
    </svg>
    <div class="back-logo">FALCRIDGE HIRES</div>
    <div class="ghost-mark"></div>
    <div class="ghost-name">FALCRIDGE HIRES</div>
    <div class="contact"><div class="contact-line">Owen Marchetti CEO 555 318-0476</div></div>
    <div class="services">Luxury Restroom Trailers Rental and Sales.<br>Weddings, Concerts, Charity, Sporting and Corp. Events.</div>
  </section>

  <section class="card card--back card--vp" aria-label="Card back, VP">
    <svg class="back-band" viewBox="0 0 487 273" aria-hidden="true">
      <polygon points="0,76 348,76 0,268" fill="var(--orange)"/>
      <line x1="348" y1="76" x2="0" y2="268" stroke="var(--edge)" stroke-width="1"/>
    </svg>
    <div class="back-logo">FALCRIDGE HIRES</div>
    <div class="ghost-mark"></div>
    <div class="ghost-name">FALCRIDGE HIRES</div>
    <div class="contact"><div class="contact-line">Leon Marchetti VP 555 318-0476</div></div>
    <div class="services">Luxury Restroom Trailers Rental and Sales.<br>Weddings, Concerts, Charity, Sporting and Corp. Events.</div>
  </section>

</main>
</body>
</html>
```